LHP Regal Business Card Design 2020

Your Manor Steward is looking for a business card that is clean and straight to the point but still looks high-end and attractive. We are a team comprised of management and field professionals focused on the high-end residential marketplace. We serve homeowners and trade professionals directly based out of the Metrowest/Boston area. We provide client services as well as construction/renovation services.
We are aiming for a black and white feel (white background and black text) and a matte finish with rounded edges.

We want to emphasis our vision of "Properties - Projects - Partners".
Dana Pellham is the president of LHP

Please include the following areas we service: Boston/Cape/Newport
Please make sure to include Dana's mobile (555) 213 4480 & office number (555) 640 1937, email dana@yourmanorsteward.example and website www.yourmanorsteward.example

Colors

Designer to choose only greyscale colors for use in the design.

Requirements
Must have
• Include "Properties - Projects - Partners" in design

Include "After Hours Emergency Support # 1800 555 0142" with icon

```html
<!DOCTYPE html>
<html lang="en">
<head>
<meta charset="utf-8">
<title>Your Manor Steward – Business Card</title>
<link rel="stylesheet" href="https://fonts.googleapis.com/css2?family=Montserrat:wght@500;600&family=Work+Sans:wght@400;500&display=swap">
<style>
  :root {
    --page: #e6e6e6;
    --card: #2a2a2a;
    --band: #d8d8d8;
    --band-text: #2b2b2b;
    --brand: #f2f2f2;
    --accent: #d4d4d4;
    --heading: #c6c6c6;
    --muted: #adadad;
    --soft: #dddddd;
    --rule: #8a8a8a;
  }
  * { box-sizing: border-box; margin: 0; padding: 0; }
  html, body { width: 1200px; height: 887px; overflow: hidden; background: var(--page); }
  .business-card {
    position: absolute; left: 100px; top: 172px;
    width: 1000px; height: 543px;
    background: var(--card);
    border-radius: 24px;
    overflow: hidden;
    font-family: "Montserrat", sans-serif;
  }
  .brand {
    position: absolute; left: 60px; top: 100px; width: 382px;
    text-align: center;
  }
  .brand-mark {
    font-weight: 600; font-size: 142px; line-height: 1;
    letter-spacing: -2px; color: var(--brand);
  }
  .brand-name {
    margin-top: 26px;
    font-weight: 600; font-size: 20px; letter-spacing: 2.2px;
    color: var(--soft); white-space: nowrap;
  }
  .divider {
    position: absolute; left: 490px; top: 94px;
    width: 1px; height: 202px; background: var(--rule);
  }
  .contact { position: absolute; left: 535px; top: 90px; }
  .person-name {
    font-weight: 600; font-size: 33px; letter-spacing: 1.5px;
    color: var(--accent); line-height: 1.1;
  }
  .person-title {
    font-family: "Work Sans", sans-serif;
    font-size: 22px; color: var(--soft); margin-top: 6px;
  }
  .contact-list { list-style: none; margin-top: 20px; }
  .contact-list li {
    display: flex; align-items: center; gap: 10px;
    font-family: "Work Sans", sans-serif;
    font-size: 22px; color: var(--soft);
    height: 31.5px; letter-spacing: 0.6px;
  }
  .contact-list svg { width: 16px; height: 16px; flex: none; }
  .emergency {
    position: absolute; left: 0; right: 0; top: 330px;
    display: flex; align-items: center; justify-content: center; gap: 10px;
    font-family: "Work Sans", sans-serif;
    font-size: 19px; letter-spacing: 0.8px; color: var(--soft);
  }
  .emergency svg { width: 22px; height: 22px; flex: none; }
  .service { position: absolute; left: 0; right: 0; top: 384px; text-align: center; }
  .service-heading {
    font-weight: 600; font-size: 28px; letter-spacing: 1.5px; color: var(--heading);
  }
  .service-areas {
    margin-top: 8px; font-family: "Work Sans", sans-serif;
    font-size: 24px; letter-spacing: 1.4px; color: var(--muted);
  }
  .service-areas .sep { color: var(--rule); padding: 0 4px; }
  .vision-band {
    position: absolute; left: 0; right: 0; bottom: 0; height: 66px;
    background: var(--band);
    display: flex; align-items: center; justify-content: center;
  }
  .vision {
    font-weight: 600; font-size: 27px; letter-spacing: 1.3px;
    color: var(--band-text); margin-left: -20px;
  }
</style>
</head>
<body>
  <div class="business-card">
    <div class="brand">
      <div class="brand-mark">LHP</div>
      <div class="brand-name">YOUR MANOR STEWARD</div>
    </div>

    <div class="divider"></div>

    <div class="contact">
      <div class="person-name">DANA PELLHAM</div>
      <div class="person-title">President</div>
      <ul class="contact-list">
        <li>
          <svg viewBox="0 0 16 16" fill="none" stroke="currentColor" stroke-width="1.4"><path d="M4 1.5l2.3 3-1.4 1.6c.8 2 2.3 3.6 4.3 4.5l1.6-1.4 3 2.3-1.4 2.4C7.6 13.6 2.4 8.4 1.6 3z"/></svg>
          (555) 213 4480
        </li>
        <li>
          <svg viewBox="0 0 16 16" fill="none" stroke="currentColor" stroke-width="1.4"><rect x="4" y="1" width="8" height="14" rx="1.5"/><line x1="7" y1="12.5" x2="9" y2="12.5"/></svg>
          (555) 640 1937
        </li>
        <li>
          <svg viewBox="0 0 16 16" fill="none" stroke="currentColor" stroke-width="1.4"><rect x="1.5" y="3.5" width="13" height="9" rx="1"/><path d="M1.5 4l6.5 5 6.5-5"/></svg>
          dana@yourmanorsteward.example
        </li>
        <li>
          <svg viewBox="0 0 16 16" fill="none" stroke="currentColor" stroke-width="1.2"><circle cx="8" cy="8" r="6.5"/><ellipse cx="8" cy="8" rx="2.8" ry="6.5"/><line x1="1.5" y1="8" x2="14.5" y2="8"/></svg>
          www.yourmanorsteward.example
        </li>
      </ul>
    </div>

    <div class="emergency">
      <svg viewBox="0 0 22 22" fill="none" stroke="currentColor" stroke-width="1.4"><circle cx="11" cy="11" r="10"/><path d="M8 5.5l1.8 2.4-1.1 1.2c.6 1.6 1.8 2.9 3.4 3.6l1.2-1.1 2.4 1.8-1.1 1.9C10.5 15 6.9 11.4 6.2 7.4z"/></svg>
      After Hours Emergency Support # 1800 555 0142
    </div>

    <div class="service">
      <div class="service-heading">WE SERVICE</div>
      <div class="service-areas">BOSTON <span class="sep">|</span> METROWEST <span class="sep">|</span> SOUTH SHORE <span class="sep">|</span> CAPE/NEWPORT</div>
    </div>

    <div class="vision-band">
      <div class="vision">PROPERTIES - PROJECTS - PARTNERS</div>
    </div>
  </div>
</body>
</html>
```